Business card design for a teacher - double sided, sleek design.

My name is Lina and I am an online Arabic language teacher. I am looking for a beautiful business card design for my online teaching business.

The cards will be printed in 85mm x 55mm size.
The card can be either portrait or landscape.

The design should contain my logo on one side and information on the other.

The design needs to be clean and modern. Use of subtle Arabic geometric patterns would be nice. Icons for the social media information on the card should also match the design theme.

My logo font is Consolas, which is a Monospace font.

Business card design should be delivered with editable PSD or EPS files in the handover.

Thanks

Lina

----

Information on the back:

URL: www.speakwithnadia.net [this should stand out more than other details]
Email: info@speakwithnadia.net
Instagram: @speakwithnadia
Facebook: facebook.com/speakwithnadia
Skype: speakwithnadia

My brand colours are shown in the logo attached. These are:
- Teal green - 4DC9C1
- Mango yellow - FFD600

Target Market(s)

- Young professionals
- Expatriates
- Women and Men

Industry/Entity Type

Education

Contact Information for Business Card

Information on the back:

Skype: speakwithnadia

- Teal green - 4DC9C1
- Mango yellow - FFD600

Font styles to use
Other font styles liked:
• Any font complimentary to my logo font which is a Monospace font called Consolas.

Colors

Designer to choose colors to be used in the design.

Requirements
Must have
• - Aesthetically pleasing look
• - Complimentary design with existing logo
Nice to have
• Arabic geometrical patterns

```html
<!DOCTYPE html>
<html lang="en">
<head>
<meta charset="utf-8">
<title>Lina Lessons – Business Card</title>
<link rel="stylesheet" href="https://fonts.googleapis.com/css2?family=Inconsolata:wght@400;500&family=Roboto:wght@400&display=swap">
<style>
  :root {
    --teal: #4dc9c1;
    --mango: #ffd600;
    --paper: #f3f3f2;
    --ink: #555555;
    --white: #ffffff;
    --backdrop: #2a2a2a;
  }
  * { box-sizing: border-box; margin: 0; padding: 0; }
  html, body {
    width: 1200px; height: 886px; overflow: hidden;
    background: var(--backdrop);
  }
  .canvas {
    width: 1200px; height: 886px;
    display: flex; flex-direction: column;
    align-items: center; justify-content: center; gap: 44px;
  }
  .card {
    position: relative;
    width: 580px; height: 375px;
    background: var(--paper);
    overflow: hidden;
    box-shadow: 0 10px 30px rgba(0,0,0,.45);
  }

  /* Wordmark: plain name with one solid dot */
  .brand {
    display: flex; align-items: center; gap: 12px;
  }
  .brand__dot {
    width: 18px; height: 18px; border-radius: 50%;
    background: var(--mango); flex: none;
  }
  .brand__name {
    font-family: "Inconsolata", monospace;
    font-weight: 500;
    font-size: 32px;
    color: var(--teal);
    white-space: nowrap;
  }

  /* Front side */
  .card--front .brand {
    position: absolute; left: 50%; top: 140px;
    transform: translateX(-50%);
  }
  .card--front .site {
    position: absolute; left: 0; right: 0; top: 262px;
    text-align: center;
    font-family: "Inconsolata", monospace;
    font-size: 15px; letter-spacing: 3px;
    color: var(--ink);
  }

  /* Back side */
  .card--back .band {
    position: absolute; left: 0; top: 0;
    width: 580px; height: 375px;
  }
  .contact {
    position: absolute; left: 26px; top: 174px;
    list-style: none;
    font-family: "Roboto", sans-serif;
    font-size: 15px; line-height: 25px;
    color: var(--white);
  }
  .contact li { display: flex; align-items: center; gap: 9px; }
  .contact__icon {
    width: 11px; height: 11px; border-radius: 50%;
    background: var(--white); flex: none;
  }
  .contact__mail { flex: none; width: 11px; }
  .contact__site { font-size: 16px; }
  .card--back .brand {
    position: absolute; right: 48px; top: 92px;
  }
  .card--back .brand__name { font-size: 30px; }
</style>
</head>
<body>
<main class="canvas">

  <section class="card card--front" aria-label="Card front">
    <div class="brand">
      <span class="brand__dot"></span>
      <span class="brand__name">Lina Lessons</span>
    </div>
    <p class="site">www.speakwithnadia.net</p>
  </section>

  <section class="card card--back" aria-label="Card back">
    <svg class="band" viewBox="0 0 580 375" aria-hidden="true">
      <polygon points="0,150 300,150 325,375 0,375" fill="var(--teal)"/>
      <polyline points="0,158 292,158 316,375" fill="none" stroke="var(--white)" stroke-width="2"/>
    </svg>
    <ul class="contact">
      <li>
        <svg class="contact__mail" height="10" viewBox="0 0 12 10" aria-hidden="true">
          <rect x="0.5" y="0.5" width="11" height="9" fill="none" stroke="#fff"/>
          <polyline points="0.5,0.5 6,5.5 11.5,0.5" fill="none" stroke="#fff"/>
        </svg>
        info@speakwithnadia.net
      </li>
      <li><span class="contact__icon"></span>@speakwithnadia</li>
      <li><span class="contact__icon"></span>/speakwithnadia</li>
      <li><span class="contact__icon"></span>speakwithnadia</li>
      <li class="contact__site"><span class="contact__icon"></span>www.speakwithnadia.net</li>
    </ul>
    <div class="brand">
      <span class="brand__dot"></span>
      <span class="brand__name">Lina Lessons</span>
    </div>
  </section>

</main>
</body>
</html>
```